TL - business card

Tallow Partners is an insurance brokerage firm, inovative, proactive, vigorous, which aims to become the leader of the insurance brokers in Anfrica. We should like to get some designs which should be avoided also in Gray / Metallic for the Administration and Orange / Blue for the Managers (ike in the picture sent). The Blue / Green logo is not the correct one, but the source of the file. Please adjust the color accordingly for the business cards. 1 / Orange / Blue 2 / Gray / Metallic We want something classic but which is transmitted strenght, inovation, modernity and most of all, rapidity. We want something start-up like, very punchy and catching eye remaining profesional at the same time. Name: Dorian Whitlock Function: Managing Director Address: N ° 17/18 Rua Veloso - R / C 2B Direita - Bairro Mutamba - Luanda Tel: (+244) 947 582 316 Email: dorian.whitlock@tallow-p.example Website: www.tallow-p. example We want classic in the front and creative, colorfull at the back. The cards will be printed in relief, with very high quality of paper.
Insurance Broker
Colors
Designer to choose colors to be used in the design.

```html
<!DOCTYPE html>
<html lang="en">
<head>
<meta charset="utf-8">
<title>Tallow Partners – Business Card</title>
<link rel="stylesheet" href="https://fonts.googleapis.com/css2?family=Montserrat:wght@400;500;600;700&display=swap">
<style>
  :root {
    --backdrop: #141414;
    --card: #1f1f1f;
    --card-edge: #2a2a2a;
    --brand-blue: #2aa7e1;
    --brand-green: #1fa25a;
    --text-light: #e8e8e8;
    --text-muted: #cfcfcf;
  }
  * { margin: 0; padding: 0; box-sizing: border-box; }
  html, body {
    width: 1200px;
    height: 900px;
    overflow: hidden;
    background: var(--backdrop);
    font-family: "Montserrat", sans-serif;
  }
  .canvas {
    position: relative;
    width: 1200px;
    height: 900px;
  }
  .card {
    position: absolute;
    left: 270px;
    width: 660px;
    height: 377px;
    background: linear-gradient(135deg, var(--card) 0%, #232323 60%, #2b2b2b 100%);
    border: 1px solid var(--card-edge);
    box-shadow: 0 18px 40px rgba(0,0,0,0.6);
  }
  .card--front { top: 50px; }
  .card--back { top: 473px; }

  .brand {
    display: flex;
    flex-direction: column;
    align-items: center;
    gap: 18px;
  }
  .brand__dot {
    width: 74px;
    height: 74px;
    border-radius: 50%;
    border: 6px solid var(--brand-green);
  }
  .brand__name {
    font-weight: 700;
    color: var(--brand-blue);
    text-transform: uppercase;
    letter-spacing: 1px;
    white-space: nowrap;
  }
  .card--front .brand {
    position: absolute;
    left: 0; right: 0;
    top: 112px;
  }
  .card--front .brand__name { font-size: 34px; }

  .card--back .brand {
    position: absolute;
    left: 30px;
    width: 300px;
    top: 110px;
  }
  .card--back .brand__name { font-size: 26px; }

  .divider {
    position: absolute;
    left: 350px;
    top: 88px;
    width: 2px;
    height: 200px;
    background: var(--brand-blue);
  }
  .contact {
    position: absolute;
    left: 382px;
    top: 92px;
    color: var(--text-light);
  }
  .contact__name {
    font-size: 28px;
    font-weight: 600;
    color: var(--brand-blue);
    letter-spacing: 1px;
  }
  .contact__role {
    font-size: 15px;
    color: var(--text-muted);
    margin-top: 2px;
    letter-spacing: 0.5px;
  }
  .contact__address {
    font-size: 15px;
    line-height: 1.5;
    margin-top: 14px;
    font-style: normal;
    letter-spacing: 0.3px;
  }
  .contact__line {
    display: flex;
    align-items: center;
    gap: 10px;
    font-size: 15px;
    margin-top: 8px;
    letter-spacing: 0.3px;
  }
  .contact__line svg { flex: none; }
</style>
</head>
<body>
<main class="canvas">

  <section class="card card--front" aria-label="Card front">
    <div class="brand">
      <span class="brand__dot"></span>
      <span class="brand__name">Tallow Partners</span>
    </div>
  </section>

  <section class="card card--back" aria-label="Card back">
    <div class="brand">
      <span class="brand__dot"></span>
      <span class="brand__name">Tallow Partners</span>
    </div>

    <div class="divider"></div>

    <div class="contact">
      <h1 class="contact__name">Dorian Whitlock</h1>
      <p class="contact__role">Managing Director</p>
      <address class="contact__address">
        N ° 17/18 Rua Veloso<br>
        R / C 2B Direita<br>
        Bairro Mutamba - Luanda
      </address>
      <p class="contact__line">
        <svg width="12" height="14" viewBox="0 0 12 14" aria-hidden="true">
          <path d="M2 1 L4.5 1 L5.5 4 L4 5 C4.6 7 5.6 8.4 7.2 9.6 L8.4 8.2 L11 9.6 L10.6 12.4 C6 12.6 1.4 7.6 2 1 Z" fill="var(--brand-blue)"/>
        </svg>
        <span>+244 947 582 316</span>
      </p>
      <p class="contact__line">
        <svg width="14" height="10" viewBox="0 0 14 10" aria-hidden="true">
          <rect x="0.75" y="0.75" width="12.5" height="8.5" fill="none" stroke="var(--brand-blue)" stroke-width="1.5"/>
          <path d="M1 1 L7 5.5 L13 1" fill="none" stroke="var(--brand-blue)" stroke-width="1.5"/>
        </svg>
        <span>dorian.whitlock@tallow-p.example</span>
      </p>
    </div>
  </section>

</main>
</body>
</html>
```